Signage Design Project

Busisness is a bakery and deli long time owned by the Tavel family. Want to develop a new outside sign that communicates it is a deli and a bakery but keeps the tavel name in the design.

The sign when produced will be about 10' by 3' . It is not lighted at present but could be if it were advantageous.

The name of the store is:

Tavel's Harbor Lane Bakery and Deli. The concept is to have a new,modern sign that reinforces that it is a deli and a bakery, as most people only know about the bakery side of the business
Updates

The name Tavel is just a reinforcer so the people kno it is still in the family.  The emphasis should be on the HARBOR LANE BAKERY and DELI

Target Market(s)

Small business breakfast and lunch customers

Industry/Entity Type

Bakery

Requirements
Must have
• Great impact from the road. Communicate that it is a deli and a bakery. Keep the Tavel name but need not be a major design element

```html
<!DOCTYPE html>
<html lang="en">
<head>
<meta charset="utf-8">
<title>Tavel's Harbor Lane Bakery and Deli – Storefront Sign</title>
<link rel="stylesheet" href="https://fonts.googleapis.com/css2?family=Courgette&family=Fredoka:wght@700&display=swap">
<style>
  :root {
    --sign-maroon: #6c262a;
    --ornament-tone: #7d3b2c;
    --lettering-yellow: #f4ea1c;
    --lettering-pale: #fffbc4;
    --lettering-shadow: rgba(40, 8, 10, 0.75);
  }
  html, body {
    margin: 0;
    padding: 0;
    overflow: hidden;
    background: var(--sign-maroon);
  }
  .sign {
    position: relative;
    width: 1200px;
    height: 360px;
    background: var(--sign-maroon);
    overflow: hidden;
  }
  .sign__ornament {
    position: absolute;
    top: 20px;
    width: 62px;
    height: 320px;
  }
  .sign__ornament--left { left: 14px; }
  .sign__ornament--right { right: 14px; }

  .sign__text {
    position: absolute;
    margin: 0;
    padding: 0 28px 8px 0;
    white-space: nowrap;
    line-height: 1;
    background: linear-gradient(180deg, var(--lettering-yellow) 0%, var(--lettering-yellow) 45%, var(--lettering-pale) 100%);
    -webkit-background-clip: text;
    background-clip: text;
    color: transparent;
    filter: drop-shadow(3px 3px 1px var(--lettering-shadow));
  }
  .sign__family {
    left: 112px;
    top: 90px;
    font-family: "Courgette", cursive;
    font-size: 50px;
  }
  .sign__location {
    left: 306px;
    top: 62px;
    font-family: "Courgette", cursive;
    font-weight: 400;
    font-size: 114px;
    letter-spacing: 1px;
  }
  .sign__trade {
    left: 184px;
    top: 210px;
    font-family: "Fredoka", sans-serif;
    font-weight: 700;
    font-size: 106px;
    letter-spacing: 2px;
  }
</style>
</head>
<body>
  <main class="sign">
    <svg class="sign__ornament sign__ornament--left" viewBox="0 0 62 320" role="img" aria-label="Decorative scrollwork border">
      <rect width="62" height="320" rx="6" fill="var(--ornament-tone)"/>
    </svg>

    <p class="sign__text sign__family">Tavel's</p>
    <h1 class="sign__text sign__location">HARBOR LANE</h1>
    <p class="sign__text sign__trade">Bakery and Deli</p>

    <svg class="sign__ornament sign__ornament--right" viewBox="0 0 62 320" role="img" aria-label="Decorative scrollwork border">
      <rect width="62" height="320" rx="6" fill="var(--ornament-tone)"/>
    </svg>
  </main>
</body>
</html>
```